Vormel Building Pty Ltd need an Identity!

We need a logo design for a building company based in Sydney, Australia. In addition - Business Card Layout. The colour scheme is to be black and red and communicate a professional yet 'hands on' approach to building.

Target Market(s)

Architects, Home Owners, Developers

Industry/Entity Type

Construction

Font styles to use
Serif
Sans Serif

Colors
ec1f27

Requirements
Must have
• Clear logo and professional direction.
Nice to have
• Use of initials as a possible logo
Should not have
• Graphics/pictures of houses, house roofs etc. Can be an abstracted form of a building.

```html
<!DOCTYPE html>
<html lang="en">
<head>
<meta charset="utf-8">
<title>Vormel Building Pty Ltd – Stationery</title>
<link rel="stylesheet" href="https://fonts.googleapis.com/css2?family=Arimo:wght@400;700&display=swap">
<style>
  :root {
    --brand-red: #ff0000;
    --brand-black: #000000;
    --paper: #ffffff;
    --edge: #a6a6a6;
    --faint-grey: #cccccc;
    --faint-red: #fdcccc;
    --ink-white: #ffffff;
  }
  * { box-sizing: border-box; margin: 0; padding: 0; }
  html, body { width: 1200px; height: 1200px; overflow: hidden; background: var(--paper); }
  body { position: relative; font-family: "Arimo", Arial, sans-serif; }

  /* Letterhead */
  .letterhead {
    position: absolute; left: 47px; top: 39px; width: 793px; height: 1122px;
    border: 1.5px solid var(--edge); background: var(--paper); overflow: hidden;
  }
  .letterhead__mark {
    position: absolute; left: 60px; top: 58px; width: 62px; height: 62px;
    background: var(--brand-black);
  }
  .letterhead__rule {
    position: absolute; left: 168px; width: 580px; height: 3px; background: var(--brand-black);
  }
  .letterhead__rule--top { top: 72px; }
  .letterhead__rule--bottom { top: 135px; }
  .letterhead__name {
    position: absolute; left: 196px; top: 78px; white-space: nowrap;
    font-weight: 700; font-size: 48px; line-height: 56px; color: var(--brand-red);
  }
  .letterhead__watermark {
    position: absolute; left: 0; right: 0; top: 560px; text-align: center;
    font-weight: 700; font-size: 60px; color: var(--faint-red); white-space: nowrap;
  }
  .letterhead__footer {
    position: absolute; left: 0; right: 0; bottom: 0; height: 93px;
    background: linear-gradient(to right, var(--brand-red) 0, var(--brand-red) 395px, var(--brand-black) 403px, var(--brand-black) 100%);
    color: var(--ink-white); font-weight: 700; font-size: 14.5px; line-height: 18px;
  }
  .letterhead__address { position: absolute; right: 414px; top: 14px; text-align: right; }
  .letterhead__contact { position: absolute; left: 417px; top: 14px; }

  /* Business card */
  .card {
    position: absolute; left: 876px; top: 362px; width: 279px; height: 476px;
  }
  .card__face {
    position: absolute; left: -98.5px; top: 98.5px; width: 476px; height: 279px;
    transform: rotate(-90deg); transform-origin: center;
    border: 1.5px solid var(--edge); background: var(--paper); overflow: hidden;
  }
  .card__mark {
    position: absolute; left: 70px; top: 40px; width: 30px; height: 30px; background: var(--brand-black);
  }
  .card__rule { position: absolute; left: 128px; width: 286px; height: 1.5px; background: var(--brand-black); }
  .card__rule--top { top: 38px; }
  .card__rule--bottom { top: 71px; }
  .card__name {
    position: absolute; left: 132px; top: 41px; white-space: nowrap;
    font-weight: 700; font-size: 21px; line-height: 28px; color: var(--brand-red);
  }
  .card__watermark {
    position: absolute; left: 0; right: 0; top: 128px; text-align: center;
    font-weight: 700; font-size: 22px; color: var(--faint-red); white-space: nowrap;
  }
  .card__person { position: absolute; left: 106px; top: 188px; color: var(--brand-red); }
  .card__person-name { font-weight: 700; font-size: 14px; line-height: 15px; }
  .card__person-role { font-weight: 700; font-size: 6px; line-height: 8px; padding-left: 14px; }
  .card__band {
    position: absolute; left: 0; right: 0; bottom: 0; height: 55px;
    background: linear-gradient(to right, var(--brand-red) 0, var(--brand-red) 236px, var(--brand-black) 240px, var(--brand-black) 100%);
    color: var(--ink-white); font-weight: 700; font-size: 8px; line-height: 11px;
  }
  .card__address { position: absolute; right: 248px; top: 8px; text-align: right; }
  .card__contact { position: absolute; left: 250px; top: 8px; }
</style>
</head>
<body>

<section class="letterhead">
  <div class="letterhead__mark"></div>
  <div class="letterhead__rule letterhead__rule--top"></div>
  <div class="letterhead__name">Vormel Building Pty Ltd</div>
  <div class="letterhead__rule letterhead__rule--bottom"></div>

  <div class="letterhead__watermark">Vormel Building Pty Ltd</div>

  <footer class="letterhead__footer">
    <div class="letterhead__address">Address : xoxoxoxo, xoxo<br>xoxoxo,<br>xoxoxo - xoxoxo</div>
    <div class="letterhead__contact">Cell : 90909090<br>E-mail : hello@vormelbuilding.com.au</div>
  </footer>
</section>

<section class="card">
  <div class="card__face">
    <div class="card__mark"></div>
    <div class="card__rule card__rule--top"></div>
    <div class="card__name">Vormel Building Pty Ltd</div>
    <div class="card__rule card__rule--bottom"></div>

    <div class="card__watermark">Vormel Building</div>

    <div class="card__person">
      <div class="card__person-name">Your Name</div>
      <div class="card__person-role">Designation</div>
    </div>

    <div class="card__band">
      <div class="card__address">Address : xoxoxoxo, xoxo<br>xoxoxo,<br>xoxoxo - xoxoxo</div>
      <div class="card__contact">Cell : 90909090<br>E-mail : hello@vormelbuilding.com.au</div>
    </div>
  </div>
</section>

</body>
</html>
```